TL - business card

Tallow Partners is an insurance brokerage firm, inovative, proactive, vigorous, which aims to become the leader of the insurance brokers in Anfrica. We should like to get some designs which should be avoided also in Gray / Metallic for the Administration and Orange / Blue for the Managers (ike in the picture sent). The Blue / Green logo is not the correct one, but the source of the file. Please adjust the color accordingly for the business cards. 1 / Orange / Blue 2 / Gray / Metallic We want something classic but which is transmitted strenght, inovation, modernity and most of all, rapidity. We want something start-up like, very punchy and catching eye remaining profesional at the same time. Name: Dorian Whitlock Function: Managing Director Address: N ° 17/18 Rua Veloso - R / C 2B Direita - Bairro Mutamba - Luanda Tel: (+244) 947 582 316 Email: dorian.whitlock@tallow-p.example Website: www.tallow-p. example We want classic in the front and creative, colorfull at the back. The cards will be printed in relief, with very high quality of paper.
Insurance Broker
Colors
Designer to choose colors to be used in the design.

```html
<!DOCTYPE html>
<html lang="en">
<head>
<meta charset="utf-8">
<title>Tallow Partners – Business Card</title>
<link rel="stylesheet" href="https://fonts.googleapis.com/css2?family=Exo+2:wght@600;700&family=Open+Sans:wght@400;600&display=swap">
<style>
  :root {
    --brand-blue: #1f9ad8;
    --brand-blue-light: #2bb0e6;
    --brand-blue-deep: #1a86c6;
    --brand-orange: #f5a31a;
    --ink-grey: #4a4a4a;
    --swoosh-grey: #b9bcc0;
    --swoosh-grey-light: #dcdee0;
    --paper: #ffffff;
    --backdrop: #e6e9ec;
  }
  * { box-sizing: border-box; margin: 0; padding: 0; }
  html, body {
    width: 1200px; height: 900px; overflow: hidden;
    background: var(--backdrop);
  }
  .canvas {
    width: 1200px; height: 900px;
    display: flex; flex-direction: column;
    align-items: center; justify-content: center; gap: 40px;
  }
  .card {
    position: relative;
    width: 700px; height: 400px;
    border-radius: 34px;
    overflow: hidden;
    box-shadow: 0 10px 24px rgba(0,0,0,0.18);
  }

  /* Front */
  .card-front { background: var(--paper); }
  .front-shapes { position: absolute; inset: 0; width: 100%; height: 100%; }
  .front-content { position: absolute; left: 46px; top: 36px; }
  .company-name {
    font-family: "Exo 2", sans-serif; font-weight: 700;
    font-size: 42px; letter-spacing: 1px; text-transform: uppercase;
    color: var(--brand-orange); line-height: 1;
  }
  .person-name {
    margin-top: 26px;
    font-family: "Exo 2", sans-serif; font-weight: 600;
    font-size: 28px; text-transform: uppercase;
    color: var(--brand-blue); line-height: 1;
  }
  .person-role {
    margin-top: 6px;
    font-family: "Open Sans", sans-serif; font-size: 18px;
    color: var(--brand-orange);
  }
  .contact-list { list-style: none; margin-top: 14px; }
  .contact-item {
    display: flex; align-items: center; gap: 10px;
    font-family: "Open Sans", sans-serif; font-size: 17px;
    color: var(--ink-grey); line-height: 1.55;
  }
  .contact-icon { width: 18px; height: 18px; flex: none; }
  .address-line {
    position: absolute; left: 40px; bottom: 20px;
    font-family: "Open Sans", sans-serif; font-size: 17px;
    color: var(--paper);
  }

  /* Back */
  .card-back {
    background: radial-gradient(ellipse at 50% 60%, var(--brand-blue-light), var(--brand-blue-deep));
    display: flex; align-items: center; justify-content: center;
  }
  .back-lockup { display: flex; align-items: center; gap: 18px; }
  .back-mark {
    width: 58px; height: 58px; border-radius: 50%;
    border: 5px solid var(--paper);
  }
  .back-name {
    font-family: "Exo 2", sans-serif; font-weight: 700;
    font-size: 44px; letter-spacing: 1px; text-transform: uppercase;
    color: var(--paper);
  }
</style>
</head>
<body>
<main class="canvas">

  <section class="card card-front" aria-label="Business card front">
    <svg class="front-shapes" viewBox="0 0 700 400" preserveAspectRatio="none" aria-hidden="true">
      <path class="swoosh-light" d="M230,250 C360,330 520,340 700,300 L700,330 C520,360 360,345 230,250 Z" fill="var(--swoosh-grey-light)"/>
      <path class="swoosh" d="M250,265 C380,340 540,350 700,318 L700,345 C540,372 380,350 250,265 Z" fill="var(--swoosh-grey)"/>
      <path class="blue-band" d="M0,210 C140,300 360,350 700,348 L700,400 L0,400 Z" fill="var(--brand-blue)"/>
    </svg>

    <div class="front-content">
      <h1 class="company-name">Tallow Partners</h1>
      <h2 class="person-name">Dorian Whitlock</h2>
      <p class="person-role">Managing Director</p>
      <ul class="contact-list">
        <li class="contact-item">
          <svg class="contact-icon" viewBox="0 0 18 18" aria-hidden="true"><circle cx="9" cy="9" r="9" fill="var(--brand-orange)"/><path d="M6 4.5 L7.6 4.5 L8.2 7 L7.2 7.8 C7.7 9 8.7 10 10 10.6 L10.8 9.6 L13.3 10.2 L13.3 11.8 C9 12.2 5.7 8.8 6 4.5 Z" fill="#fff"/></svg>
          (+244) 947 582 316
        </li>
        <li class="contact-item">
          <svg class="contact-icon" viewBox="0 0 18 18" aria-hidden="true"><circle cx="9" cy="9" r="9" fill="var(--brand-orange)"/><rect x="4.5" y="6" width="9" height="6.5" fill="#fff"/><path d="M4.5 6 L9 9.6 L13.5 6" stroke="var(--brand-orange)" stroke-width="1" fill="none"/></svg>
          dorian.whitlock@tallow-p.example
        </li>
        <li class="contact-item">
          <svg class="contact-icon" viewBox="0 0 18 18" aria-hidden="true"><circle cx="9" cy="9" r="9" fill="var(--brand-orange)"/><circle cx="9" cy="9" r="4.8" fill="none" stroke="#fff" stroke-width="1.2"/><path d="M4.2 9 H13.8 M9 4.2 C6.8 7 6.8 11 9 13.8 M9 4.2 C11.2 7 11.2 11 9 13.8" stroke="#fff" stroke-width="1" fill="none"/></svg>
          www.tallow-p. example
        </li>
      </ul>
    </div>

    <p class="address-line">N ° 17/18 Rua Veloso - R / C 2B Direita - Bairro Mutamba - Luanda</p>
  </section>

  <section class="card card-back" aria-label="Business card back">
    <div class="back-lockup">
      <span class="back-mark" aria-hidden="true"></span>
      <span class="back-name">Tallow Partners</span>
    </div>
  </section>

</main>
</body>
</html>
```